Business Card Design For Marketing Agnecy LVP

Need business card design for marketing agency.

Doug Fenwick
President, CEO
1-555-302-4196
doug@boldpromoperksgroup.example
www.BoldPromoPerksGroup.example

Back Side:
Boost Sales Using Rewards, Incentives & Giveaways
Get A Free Sample Package

Target Market(s)

B2B

Industry/Entity Type

Marketing

Contact Information for Business Card

Doug Fenwick
President, CEO
1-555-302-4196

Back Side:
Get A Free Sample Package

Please note that my current url is OLD DESIGN. I am working on new design and want the business card to match color themes at least on new site. Here is the demo link for new site so you can see the colors I use, etc.

http://layoutcratehub.example/kq/doug/lvp_final/index.html

Requirements
Must have
• Please note that my current url is OLD DESIGN. I am working on new design and want the business card to match color themes at least on new site. Here is the demo link for new site so you can see the colors I use, etc.

Nice to have

Should not have

```html
<!DOCTYPE html>
<html lang="en">
<head>
<meta charset="utf-8">
<title>LVP Business Card</title>
<link href="https://fonts.googleapis.com/css2?family=Raleway:wght@500;700&family=Arimo:wght@400&display=swap" rel="stylesheet">
<style>
  :root {
    --brand-blue: #1b75bc;
    --brand-grey: #58595b;
    --ink: #3a3a3c;
    --paper: #ffffff;
    --backdrop: #d9d9db;
  }
  html, body {
    margin: 0;
    padding: 0;
    width: 1200px;
    height: 802px;
    overflow: hidden;
    background: var(--backdrop);
  }
  .canvas {
    position: relative;
    width: 1200px;
    height: 802px;
  }
  .card {
    position: absolute;
    top: 274px;
    width: 442px;
    height: 264px;
    overflow: hidden;
  }
  .card-front { left: 136px; background: var(--paper); }
  .card-back { left: 624px; background: var(--brand-blue); }

  .front-band {
    position: absolute;
    left: 0; top: 0;
    width: 50px; height: 100%;
    background: var(--brand-blue);
  }
  .front-rule {
    position: absolute;
    left: 52px; top: 0;
    width: 3px; height: 100%;
    background: var(--brand-grey);
  }
  .brand-mark {
    position: absolute;
    left: 262px; top: 58px;
    width: 146px;
    display: flex;
    align-items: center;
    justify-content: flex-end;
    gap: 8px;
  }
  .brand-dot {
    width: 12px; height: 12px;
    border-radius: 50%;
    background: var(--brand-blue);
  }
  .brand-name {
    font-family: 'Raleway', sans-serif;
    font-weight: 700;
    font-size: 64px;
    line-height: 1;
    color: var(--brand-blue);
    letter-spacing: 1px;
  }
  .person {
    position: absolute;
    left: 71px; top: 140px;
  }
  .person-name {
    font-family: 'Raleway', sans-serif;
    font-weight: 700;
    font-size: 15.5px;
    color: var(--brand-blue);
    margin: 0;
    line-height: 1.1;
  }
  .person-title {
    font-family: 'Arimo', sans-serif;
    font-size: 13px;
    color: var(--ink);
    margin: 1px 0 0;
  }
  .contact {
    position: absolute;
    left: 72px; top: 194px;
    margin: 0; padding: 0;
    list-style: none;
    font-family: 'Arimo', sans-serif;
    font-size: 12.2px;
    color: var(--ink);
  }
  .contact li {
    display: flex;
    align-items: center;
    gap: 4px;
    height: 16px;
  }
  .contact svg { width: 11px; height: 11px; fill: var(--brand-blue); flex: none; }
  .contact .web-accent { color: var(--brand-blue); }

  .back-pitch {
    position: absolute;
    left: 0; top: 84px;
    width: 100%;
    text-align: center;
    font-family: 'Raleway', sans-serif;
    font-weight: 500;
    font-size: 16.5px;
    line-height: 28.5px;
    color: var(--paper);
    margin: 0;
  }
  .back-strip {
    position: absolute;
    left: 0; top: 194px;
    width: 100%; height: 47px;
    background: var(--brand-grey);
    display: flex;
    align-items: center;
    justify-content: center;
    font-family: 'Arimo', sans-serif;
    font-size: 15.5px;
    color: var(--paper);
  }
</style>
</head>
<body>
<div class="canvas">
  <section class="card card-front" aria-label="Business card front">
    <div class="front-band"></div>
    <div class="front-rule"></div>
    <div class="brand-mark">
      <span class="brand-name">LVP</span>
      <span class="brand-dot"></span>
    </div>
    <div class="person">
      <h1 class="person-name">DOUG FENWICK</h1>
      <p class="person-title">President, CEO</p>
    </div>
    <ul class="contact">
      <li>
        <svg viewBox="0 0 12 12" aria-hidden="true"><path d="M1 3.5C1 2 2.5 1.5 6 1.5S11 2 11 3.5V5H8.5V4H3.5V5H1Z"/><rect x="2.5" y="5.5" width="7" height="5" rx="1"/></svg>
        1-555-302-4196
      </li>
      <li>
        <svg viewBox="0 0 12 12" aria-hidden="true"><path d="M1 2.5H11V9.5H1Z M1.8 3.3 6 6.6 10.2 3.3" fill="none" stroke="#1b75bc" stroke-width="1.2"/></svg>
        doug@boldpromoperksgroup.example
      </li>
      <li>
        <svg viewBox="0 0 12 12" aria-hidden="true"><circle cx="6" cy="6" r="5.2"/><path d="M3.5 4.5 5 3.5 6.5 5 5.5 6.5 7 8.5 6 10M8 2.5 9 4.5 10.5 5" fill="none" stroke="#fff" stroke-width="0.9"/></svg>
        <span>www.<span class="web-accent">BoldPromoPerksGroup</span>.example</span>
      </li>
    </ul>
  </section>

  <section class="card card-back" aria-label="Business card back">
    <p class="back-pitch">BOOST SALES USING REWARDS<br>INCENTIVES &amp; GIVEAWAYS<br>GET A FREE SAMPLE PACKAGE</p>
    <div class="back-strip">www.BoldPromoPerksGroup.example</div>
  </section>
</div>
</body>
</html>
```